Communication and Marketing agency needs a new presentation card

We are a group of communication and marketing agencies specialized in companies that are in the logistics and industrial sector. The head agency is TELVANO Grupo and the group consists of 4 agencies: TELVANO Media, TELVANO Digital, TELVANO Research and DifundeEnPantalla. We hace 4 offices in Spain (Madrid, Barcelona, Valencia and Murcia). We are looking for a clean and attractive design that transmits our experience, brand presence in the market and knowledge to those who receive the card.It has to maintain the colors of the logo that is attached.
Target Market(s)
logistics and industrial sector
Marketing department
Contact Information for Business Card
Clean and attractive design

```html
<!DOCTYPE html>
<html lang="en">
<head>
<meta charset="utf-8">
<title>TELVANO Grupo – Business Card</title>
<link rel="stylesheet" href="https://fonts.googleapis.com/css2?family=Oswald:wght@500&family=Open+Sans:wght@400;600&display=swap">
<style>
  :root {
    --brand-red: #b31e2b;
    --ink-dark: #4a4a4a;
    --ink-black: #111111;
    --card-white: #f3f3f3;
    --backdrop: #e6e3df;
  }
  * { margin: 0; padding: 0; box-sizing: border-box; }
  html, body { width: 1200px; height: 971px; overflow: hidden; }
  body { background: var(--backdrop); position: relative; font-family: "Open Sans", sans-serif; }

  .card {
    position: absolute;
    width: 560px;
    height: 320px;
    border-radius: 3px;
    overflow: hidden;
    box-shadow: 0 6px 18px rgba(0,0,0,.18);
  }
  .card-front { left: 140px; top: 95px; background: var(--brand-red); }
  .card-back  { left: 500px; top: 540px; background: var(--card-white); }

  .brand-name {
    font-family: "Oswald", sans-serif;
    font-weight: 500;
    letter-spacing: 1px;
    white-space: nowrap;
  }
  .card-front .brand-name {
    position: absolute; left: 0; right: 0; top: 118px;
    text-align: center; font-size: 54px; color: #ffffff; line-height: 1;
  }

  .card-back .brand-name {
    position: absolute; left: 64px; top: 110px;
    font-size: 32px; color: var(--brand-red); line-height: 1;
  }
  .divider {
    position: absolute; left: 290px; top: 62px;
    width: 2px; height: 128px; background: var(--brand-red);
  }
  .contact { position: absolute; left: 310px; top: 56px; color: var(--ink-dark); }
  .person-name {
    font-family: "Oswald", sans-serif; font-weight: 500;
    font-size: 21px; letter-spacing: 1px; color: var(--brand-red); line-height: 1.1;
  }
  .person-role { font-size: 14px; line-height: 1.3; margin-bottom: 7px; }
  .address { font-size: 11.5px; line-height: 1.45; margin-left: 8px; margin-bottom: 7px; }
  .line { display: flex; align-items: center; gap: 6px; font-size: 11.5px; line-height: 1.5; margin-left: 8px; }
  .line svg { width: 10px; height: 10px; fill: var(--brand-red); flex: none; }

  .wave { position: absolute; left: 0; top: 0; width: 560px; height: 320px; }
  .website {
    position: absolute; right: 40px; top: 262px;
    font-size: 13px; font-weight: 600; color: #ffffff; letter-spacing: .5px;
    transform: rotate(-6deg); transform-origin: right center;
  }
</style>
</head>
<body>

  <section class="card card-front">
    <div class="brand-name">TELVANO Grupo</div>
  </section>

  <section class="card card-back">
    <svg class="wave" viewBox="0 0 560 320" aria-hidden="true">
      <path d="M40,287 C180,282 300,264 390,234 C450,214 510,206 560,207" fill="none" stroke="var(--ink-black)" stroke-width="5"/>
      <path d="M0,292 C160,288 300,270 395,239 C455,219 515,214 560,215 L560,320 L0,320 Z" fill="var(--brand-red)"/>
    </svg>

    <div class="brand-name">TELVANO Grupo</div>
    <div class="divider"></div>

    <div class="contact">
      <div class="person-name">ADRIAN NAVARRO</div>
      <div class="person-role">Founder</div>
      <div class="address">Calle Alcalá 214, 3º<br>28028 Madrid, Spain</div>
      <div class="line">
        <svg viewBox="0 0 24 24"><path d="M6.6 10.8a15.1 15.1 0 0 0 6.6 6.6l2.2-2.2c.3-.3.7-.4 1-.2 1.1.4 2.3.6 3.6.6.6 0 1 .4 1 1V20c0 .6-.4 1-1 1A17 17 0 0 1 3 4c0-.6.4-1 1-1h3.5c.6 0 1 .4 1 1 0 1.3.2 2.5.6 3.6.1.3 0 .7-.2 1z"/></svg>
        <span>(000) 914-270-55</span>
      </div>
      <div class="line">
        <svg viewBox="0 0 24 24"><path d="M2 5h20v2l-10 6L2 7zM2 9l10 6 10-6v10H2z"/></svg>
        <span>info@telvanogrupo.com</span>
      </div>
    </div>

    <div class="website">telvanogrupo.com</div>
  </section>

</body>
</html>
```